Card Design for my dog training business Brightpaw Obedience

Need a business card design for my dog training business with my new logo. Want the card to come off professional yet fun. Want it to be very eye catchy as well. I normally have these at vet clinics, pet stores, and groomers. so need it to look better than my competitors.
Target Market(s)
dog owners
Industry/Entity Type
Dog Training
Contact Information for Business Card
needs logo, my name and info
Font styles to use
Serif
Colors
0255a3
ffffff
ec1f27
000000
333333
fbfbfb
Requirements
Must have
- Brightpaw Obedience
- Felix Orland
- 415 903 2276
- info@brightpawobedience.example
- www.brightpawobedience.example

```html
<!DOCTYPE html>
<html lang="en">
<head>
<meta charset="utf-8">
<title>Brightpaw Obedience — Business Card</title>
<link href="https://fonts.googleapis.com/css2?family=Libre+Baskerville:wght@400;700&display=swap" rel="stylesheet">
<style>
  :root {
    --brand-blue: #0e5d80;
    --brand-blue-deep: #0a4d6c;
    --ink: #333333;
    --paper: #ffffff;
    --stage: #ececec;
    --serif: "Libre Baskerville", Georgia, serif;
  }
  * { box-sizing: border-box; margin: 0; padding: 0; }
  html, body {
    width: 1200px; height: 900px; overflow: hidden;
    background: var(--stage);
    font-family: var(--serif);
  }
  .canvas {
    position: relative; width: 1200px; height: 900px;
    display: flex; flex-direction: column; align-items: center; justify-content: center; gap: 40px;
  }
  .card {
    position: relative; width: 630px; height: 360px; overflow: hidden;
    box-shadow: 0 6px 18px rgba(0,0,0,.18);
  }

  /* Front */
  .card--front { background: var(--brand-blue); color: var(--paper); }
  .front-watermark {
    position: absolute; right: 30px; top: 36px;
    font-size: 38px; line-height: 1; color: rgba(255,255,255,.09);
    white-space: nowrap;
  }
  .front-logo {
    position: absolute; left: 0; right: 0; top: 120px;
    display: flex; align-items: center; justify-content: center; gap: 12px;
  }
  .front-logo .mark-dot { width: 14px; height: 14px; border-radius: 50%; background: var(--paper); }
  .front-logo .brand-name { font-size: 26px; color: var(--paper); }
  .front-url {
    position: absolute; left: 0; right: 0; top: 270px; text-align: center;
    font-size: 15px; letter-spacing: .3px;
  }

  /* Back */
  .card--back { background: var(--paper); color: var(--ink); }
  .back-logo {
    position: absolute; left: 44px; top: 130px;
    display: flex; align-items: center; gap: 10px;
  }
  .back-logo .mark-dot { width: 12px; height: 12px; border-radius: 50%; background: var(--brand-blue); }
  .back-logo .brand-name { font-size: 20px; color: var(--brand-blue); }
  .holder {
    position: absolute; right: 44px; top: 40px; text-align: right;
  }
  .holder-name {
    font-size: 16px; color: var(--brand-blue); letter-spacing: .6px; text-transform: uppercase;
  }
  .holder-role { font-size: 12px; color: var(--ink); margin-top: 4px; }
  .rule { position: absolute; height: 1px; background: var(--brand-blue); }
  .rule--name { right: 44px; top: 86px; width: 240px; }
  .rule--contact { left: 44px; right: 44px; top: 226px; }
  .contacts {
    position: absolute; left: 44px; top: 250px;
    list-style: none; display: flex; flex-direction: column; gap: 9px;
  }
  .contacts li { display: flex; align-items: center; gap: 12px; font-size: 14px; color: var(--ink); }
  .contact-icon { width: 18px; height: 18px; flex: none; }
</style>
</head>
<body>
<main class="canvas">
  <section class="card card--front" aria-label="Card front">
    <div class="front-watermark" aria-hidden="true">Brightpaw Obedience</div>
    <div class="front-logo">
      <span class="mark-dot"></span>
      <span class="brand-name">Brightpaw Obedience</span>
    </div>
    <p class="front-url">www.brightpawobedience.example</p>
  </section>

  <section class="card card--back" aria-label="Card back">
    <div class="back-logo">
      <span class="mark-dot"></span>
      <span class="brand-name">Brightpaw Obedience</span>
    </div>
    <div class="holder">
      <p class="holder-name">Felix Orland</p>
      <p class="holder-role">Owner</p>
    </div>
    <div class="rule rule--name"></div>
    <div class="rule rule--contact"></div>
    <ul class="contacts">
      <li>
        <svg class="contact-icon" viewBox="0 0 18 18" aria-hidden="true"><circle cx="9" cy="9" r="9" fill="#0e5d80"/><path d="M6 5.2l1.6-.4 1 2.2-1 .7c.5 1.1 1.3 1.9 2.4 2.4l.7-1 2.2 1-.4 1.6c-3.3.2-6.7-3.2-6.5-6.5z" fill="#fff"/></svg>
        <span>415 903 2276</span>
      </li>
      <li>
        <svg class="contact-icon" viewBox="0 0 18 18" aria-hidden="true"><circle cx="9" cy="9" r="9" fill="#0e5d80"/><rect x="4.5" y="6" width="9" height="6.5" fill="none" stroke="#fff" stroke-width="1.1"/><path d="M4.5 6l4.5 3.6L13.5 6" fill="none" stroke="#fff" stroke-width="1.1"/></svg>
        <span>info@brightpawobedience.example</span>
      </li>
      <li>
        <svg class="contact-icon" viewBox="0 0 18 18" aria-hidden="true"><circle cx="9" cy="9" r="9" fill="#0e5d80"/><circle cx="9" cy="9" r="4.6" fill="none" stroke="#fff" stroke-width="1"/><path d="M4.4 9h9.2M9 4.4c-2 2.6-2 6.6 0 9.2M9 4.4c2 2.6 2 6.6 0 9.2" fill="none" stroke="#fff" stroke-width=".9"/></svg>
        <span>www.brightpawobedience.example</span>
      </li>
    </ul>
  </section>
</main>
</body>
</html>
```